Meadow Kr Circle (company name is Meadow Kr Circle LLP)

management of homestay, hospitality something similar with https://www.dorvika.example

Target Market(s)

johor bahru market (Malaysia)

Contact Information for Business Card

Meadow Circle KR LLP

Logo Text

eyes catching, attractive, amazing, Nice, jaw dropping for design

Coding

Coded - Design and coding required

Number of Pages Required

5+ page

Colors

Designer to choose colors to be used in the design.

Requirements
Must have
• please change the short term proposal to our company logo and change the name from dorvika to meadow KR Circle LLP
• thanks
Nice to have
• please let me have eyes catching , jaw dropping design

```html
<!DOCTYPE html>
<html lang="en">
<head>
<meta charset="utf-8">
<title>Kr Meadow Circle — Short-stay Rental Management</title>
<link href="https://fonts.googleapis.com/css2?family=Poppins:wght@400;500;600;700&family=Roboto:wght@400;500;700&display=swap" rel="stylesheet">
<style>
:root{
  --teal:#0d7a84;
  --teal-dark:#0a6169;
  --teal-soft:#5fa9ae;
  --coral:#f1545a;
  --ink:#222a2c;
  --grey:#8a8f91;
  --white:#ffffff;
}
*{margin:0;padding:0;box-sizing:border-box}
html,body{width:1200px;height:4167px;overflow:hidden}
body{position:relative;font-family:'Roboto',sans-serif;color:var(--ink);background:var(--white)}
.abs{position:absolute}
.center{left:0;width:1200px;text-align:center}
h2.section-title{font-family:'Poppins',sans-serif;font-weight:700;font-size:26px;letter-spacing:.5px;color:var(--ink)}
.rule{height:3px;background:var(--teal);width:64px}

/* hero */
.hero{left:0;top:0;width:1200px;height:597px;background:linear-gradient(180deg,#4a9ca2 0%,#2f8b93 55%,#1f7f88 100%)}
.logo{left:89px;top:38px;color:var(--white);font-family:'Poppins',sans-serif;font-weight:500;font-size:19px;letter-spacing:.5px;line-height:1.1;display:flex;align-items:center;gap:10px}
.logo .mark{width:14px;height:14px;border-radius:50%;background:var(--white)}
.nav{left:370px;top:57px;display:flex;gap:26px;color:var(--white);font-size:14px;font-weight:500}
.social-top{left:1024px;top:56px;display:flex;gap:12px}
.social-top span{width:18px;height:18px;border-radius:50%;border:2px solid var(--white)}
.welcome{top:208px;color:var(--white);font-size:20px;font-family:'Poppins',sans-serif}
.hero-title{top:240px;color:var(--white);font-family:'Poppins',sans-serif;font-weight:600;font-size:50px}
.hero-sub{top:314px;color:var(--white);font-size:21px}
.btn-outline{left:503px;top:403px;width:194px;height:47px;border:3px solid var(--white);color:var(--white);font-family:'Poppins',sans-serif;font-weight:500;font-size:19px;display:flex;align-items:center;justify-content:center}

/* about */
.about-photo{left:231px;top:695px;width:414px;height:414px;background:linear-gradient(135deg,#6e7378 0%,#a7abae 55%,#5e6367 100%)}
.about-box{left:556px;top:653px;width:411px;height:414px;background:linear-gradient(45deg,var(--coral) 0%,#a06570 45%,var(--teal) 100%);color:var(--white);padding:38px 32px}
.about-box h3{font-family:'Poppins',sans-serif;font-weight:600;font-size:24px}
.about-box .mini-rule{width:68px;height:2px;background:var(--white);margin:4px 0 14px}
.about-box p{font-size:16px;line-height:32.5px}
.read-more{left:792px;top:1010px;color:var(--white);font-size:16px;font-weight:500;display:flex;align-items:center;gap:10px}
.read-more i{width:22px;height:22px;border:2px solid var(--white);border-radius:50%;display:inline-flex;align-items:center;justify-content:center}

/* why */
.why-band{left:0;top:1333px;width:1200px;height:395px;background:var(--teal)}
.why-photo{left:89px;top:1286px;width:498px;height:487px;background:linear-gradient(160deg,#f1cf8d 0%,#c9a57a 45%,#8e8a7a 100%)}
.why-list{left:647px;top:1343px;list-style:none;color:var(--white);font-family:'Poppins',sans-serif;font-weight:600;font-size:22px;line-height:54px;width:370px}
.why-list li{position:relative;padding-left:30px}
.why-list li::before{content:"";position:absolute;left:0;top:22px;width:11px;height:11px;background:var(--white)}

/* values */
.note-icon{left:569px;top:1900px;width:62px;height:64px;background:var(--teal);display:flex;align-items:center;justify-content:center}
.values-title{top:1986px;font-family:'Poppins',sans-serif;font-weight:600;font-size:21px}
.values-title em{font-style:normal;color:var(--teal)}
.timeline-line{left:596px;top:2060px;width:2px;height:410px;background:var(--teal)}
.step{left:581px;width:32px;height:32px;border:2px solid var(--teal);background:var(--white);color:var(--teal);font-family:'Poppins',sans-serif;font-weight:600;font-size:17px;display:flex;align-items:center;justify-content:center}
.step.end{background:var(--teal)}
.step.end::after{content:"";width:12px;height:12px;background:var(--coral)}
.note{font-size:15px;color:#555;line-height:42px}
.note.right{left:656px;width:285px}
.note.left{left:256px;width:280px;text-align:right}

/* how to start */
.start{left:0;top:2561px;width:1200px;height:445px;background:linear-gradient(180deg,#2e8d95 0%,#137e88 100%)}
.start-title{top:2602px;color:var(--white);font-family:'Poppins',sans-serif;font-weight:600;font-size:26px}
.stage{width:240px;text-align:center;color:var(--white)}
.stage .ring{width:188px;height:188px;margin:0 auto;border:4px solid var(--white);border-radius:50%;display:flex;align-items:center;justify-content:center}
.stage .num{font-family:'Poppins',sans-serif;font-weight:600;font-size:32px;line-height:1;margin-top:14px}
.stage .label{font-family:'Poppins',sans-serif;font-weight:600;font-size:14px;line-height:22px}

/* pricing */
.pricing-lead{top:3152px;color:var(--grey);font-size:22px;line-height:34px}
.plan{background:var(--white);box-shadow:0 4px 18px rgba(0,0,0,.12);text-align:center}
.plan h4{font-family:'Poppins',sans-serif;font-weight:600;font-size:14px;color:var(--teal);margin:22px 0 12px}
.plan ul{list-style:none;font-size:15px;font-weight:500;line-height:32px;color:#333}
.price-pill{display:inline-block;background:var(--teal);color:var(--white);font-size:12px;font-weight:700;border-radius:20px;padding:9px 22px;margin-top:16px}
.conditions{font-size:11px;color:#777;margin-top:8px}
.plan-featured{left:458px;top:3286px;width:284px;height:428px;background:linear-gradient(180deg,var(--coral) 0%,#a3616c 42%,var(--teal) 100%);color:var(--white);text-align:center;border-radius:4px;box-shadow:0 6px 22px rgba(0,0,0,.2)}
.plan-featured h4{font-family:'Poppins',sans-serif;font-weight:600;font-size:19px;margin:46px 0 14px}
.plan-featured ul{list-style:none;font-size:14.5px;line-height:32.5px}
.pill-white{display:inline-block;background:var(--white);color:var(--teal);font-family:'Poppins',sans-serif;font-weight:600;font-size:20px;border-radius:26px;padding:7px 32px;margin-top:16px}
.plan-featured .conditions{color:var(--white);margin-top:12px}

/* footer */
.skyline{left:0;top:3778px;width:1200px;height:84px;background:linear-gradient(180deg,#ffffff 0%,#7fbfc4 55%,var(--teal) 100%)}
.footer{left:0;top:3861px;width:1200px;height:270px;background:var(--teal);color:var(--white)}
.footer-logo{top:3910px;font-family:'Poppins',sans-serif;font-weight:500;font-size:30px;color:var(--white);letter-spacing:1px}
.footer-nav{top:3982px;display:flex;justify-content:center;gap:26px;font-size:14px;font-weight:500;color:var(--white)}
.contact-line{top:4032px;display:flex;justify-content:center;gap:22px;font-size:14px;color:var(--white);align-items:center}
.contact-line span{display:inline-flex;align-items:center;gap:6px}
.follow{top:4080px;display:flex;justify-content:center;align-items:center;gap:14px;color:var(--white);font-size:14px}
.follow i{width:30px;height:30px;border-radius:50%;background:#2c9fd9;display:inline-block}
.follow i.red{background:var(--coral)}
.copyright{left:0;top:4131px;width:1200px;height:36px;background:var(--coral);color:var(--white);font-size:13px;display:flex;align-items:center;justify-content:center}
</style>
</head>
<body>

<!-- Hero -->
<div class="abs hero" role="img" aria-label="Bright living room interior with teal overlay"></div>
<div class="abs logo"><span class="mark"></span>KR MEADOW CIRCLE</div>
<nav class="abs nav"><span>HOME</span><span>ABOUT US</span><span>SERVICES</span><span>BLOG</span><span>PRICING</span><span>CONTACT US</span></nav>
<div class="abs social-top"><span></span><span></span><span></span></div>
<div class="abs center welcome">WELCOME TO</div>
<h1 class="abs center hero-title">KR MEADOW CIRCLE</h1>
<div class="abs center hero-sub">Maximize your rental income</div>
<div class="abs btn-outline">GET IN TOUCH</div>

<!-- About -->
<div class="abs about-photo" role="img" aria-label="Small model houses with keys on a wooden table"></div>
<section class="abs about-box">
  <h3>ABOUT US</h3>
  <div class="mini-rule"></div>
  <p>We are a short-term rental management and provides hospitality services to help property owners<br>maximise their rental income.<br>Our goal is to help you reap the most from your rental income without you having to do any of the hard work.</p>
</section>
<div class="abs read-more">Read more <i><svg width="8" height="10" viewBox="0 0 8 10"><path d="M2 1l4 4-4 4" stroke="#fff" stroke-width="1.6" fill="none"/></svg></i></div>

<!-- Why -->
<h2 class="abs center section-title" style="top:1200px">WHY SHORT-STAY RENTAL?</h2>
<div class="abs rule" style="left:568px;top:1244px"></div>
<div class="abs why-band"></div>
<div class="abs why-photo" role="img" aria-label="Family sitting together under a cardboard roof in warm sunlight"></div>
<ul class="abs why-list">
  <li>Higher rental income potential</li>
  <li>Well maintain house condition</li>
  <li>New trend</li>
  <li>High demands</li>
  <li>Immediate monthly income</li>
  <li>Owner get 10-nights FREE stay per annum.</li>
</ul>

<!-- Things to take note -->
<h2 class="abs center section-title" style="top:1838px">THINGS TO TAKE NOTE?</h2>
<div class="abs note-icon">
  <svg width="32" height="34" viewBox="0 0 32 34"><rect x="4" y="3" width="20" height="26" rx="2" fill="none" stroke="#fff" stroke-width="2.4"/><path d="M9 10h10M9 15h10M9 20h6" stroke="#fff" stroke-width="2.2"/><path d="M20 28l9-9 2 2-9 9h-2z" fill="#fff"/></svg>
</div>
<div class="abs rule" style="left:569px;top:1972px;width:62px;height:2px"></div>
<div class="abs center values-title">OUR <em>VALUES</em></div>
<div class="abs rule" style="left:570px;top:2024px;width:60px;height:2px"></div>
<div class="abs timeline-line"></div>
<div class="abs step" style="top:2046px">1</div>
<div class="abs step" style="top:2148px">2</div>
<div class="abs step" style="top:2248px">3</div>
<div class="abs step" style="top:2354px">4</div>
<div class="abs step end" style="top:2454px"></div>
<p class="abs note right" style="top:2041px">Interior design &amp; Furnishing of the house play</p>
<p class="abs note left" style="top:2143px">All rate shown in later project</p>
<p class="abs note right" style="top:2235px">Cleaning fee will be charge extra to guests on</p>
<p class="abs note left" style="top:2349px">Meadow KR Circle takes 30% profit sharing, whereas</p>

<!-- How to start -->
<section class="abs start" role="img" aria-label="Living room interior with teal overlay"></section>
<h2 class="abs center start-title">HOW TO START?</h2>
<div class="abs stage" style="left:83px;top:2678px">
  <div class="ring"><svg width="80" height="90" viewBox="0 0 80 90"><rect x="10" y="10" width="60" height="76" rx="5" fill="#fff"/><rect x="28" y="4" width="24" height="12" rx="3" fill="#fff" stroke="#137e88" stroke-width="3"/><path d="M20 34l5 5 9-9M20 52l5 5 9-9M20 70l5 5 9-9" stroke="#137e88" stroke-width="4" fill="none"/><path d="M42 36h18M42 54h18M42 72h18" stroke="#137e88" stroke-width="4"/></svg></div>
  <div class="num">1</div><div class="label">GETTING<br>THE REQUIRED ITEMS</div>
</div>
<div class="abs stage" style="left:355px;top:2678px">
  <div class="ring"><svg width="96" height="80" viewBox="0 0 96 80"><rect x="22" y="4" width="48" height="32" rx="3" fill="#fff"/><rect x="42" y="36" width="8" height="8" fill="#fff"/><rect x="6" y="46" width="84" height="8" fill="#fff"/><rect x="10" y="54" width="8" height="24" fill="#fff"/><rect x="56" y="54" width="30" height="24" fill="#fff"/><path d="M60 64h22" stroke="#137e88" stroke-width="3"/></svg></div>
  <div class="num">2</div><div class="label">RENOVATION &amp;<br>FURNISHING</div>
</div>
<div class="abs stage" style="left:624px;top:2678px">
  <div class="ring"><svg width="96" height="86" viewBox="0 0 96 86"><path d="M48 4L6 40h10v42h64V40h10z" fill="#fff"/><rect x="30" y="44" width="36" height="34" fill="#137e88"/><path d="M36 52h24M36 60h24M36 68h16" stroke="#fff" stroke-width="3"/><rect x="40" y="22" width="16" height="12" fill="#137e88"/></svg></div>
  <div class="num">3</div><div class="label">SIGN A MANAGEMENT<br>AGREEMENT</div>
</div>
<div class="abs stage" style="left:894px;top:2678px">
  <div class="ring"><svg width="96" height="90" viewBox="0 0 96 90"><rect x="10" y="10" width="46" height="76" fill="#fff"/><g fill="#137e88"><rect x="18" y="18" width="8" height="8"/><rect x="30" y="18" width="8" height="8"/><rect x="42" y="18" width="8" height="8"/><rect x="18" y="32" width="8" height="8"/><rect x="30" y="32" width="8" height="8"/><rect x="42" y="32" width="8" height="8"/><rect x="18" y="46" width="8" height="8"/><rect x="30" y="46" width="8" height="8"/><rect x="42" y="46" width="8" height="8"/><rect x="27" y="66" width="12" height="20"/></g><circle cx="72" cy="30" r="14" fill="#fff"/><path d="M72 20v20M77 24h-7a3 3 0 000 6h4a3 3 0 010 6h-8" stroke="#137e88" stroke-width="2.4" fill="none"/><rect x="62" y="52" width="22" height="34" fill="#fff"/></svg></div>
  <div class="num">4</div><div class="label">HANDOVER KEYS &amp;<br>ACCESS CARDS</div>
</div>

<!-- Pricing -->
<h2 class="abs center section-title" style="top:3080px">PRICING</h2>
<p class="abs center pricing-lead">Lorem Ipsum is simply dummy text of the printing and<br>typesetting industry.</p>
<div class="abs plan" style="left:167px;top:3361px;width:291px;height:278px">
  <h4>SIMPLICITY PACKAGE</h4>
  <ul><li>Ceiling</li><li>Electrical Works</li><li>Carpentry Works</li><li>Resilient flooring</li></ul>
  <span class="price-pill">RM 6,000.00</span>
  <div class="conditions">* Conditions Apply</div>
</div>
<div class="abs plan" style="left:742px;top:3361px;width:291px;height:278px">
  <h4>FURNITURE PACKAGE</h4>
  <ul><li>Sofa bed</li><li>Coffee table</li><li>Dining table set</li><li>Microfiber pillows</li></ul>
  <span class="price-pill">RM 9,9000.00</span>
  <div class="conditions">* Conditions Apply</div>
</div>
<div class="abs plan-featured">
  <h4>ECONOMIC PACKAGE</h4>
  <ul><li>Full Height Day &amp; Night curtain</li><li>Main Entrance Door Grill</li><li>Supply &amp; Install LED</li><li>Surface LightSupply &amp; I</li><li>nstall Down Light</li><li>Supply &amp; Install Ceiling Fan</li><li>Retractive Hanging Rack</li></ul>
  <span class="pill-white">RM 7,950.00</span>
  <div class="conditions">* Conditions Apply</div>
</div>

<!-- Footer -->
<div class="abs skyline" role="img" aria-label="City skyline silhouette in teal"></div>
<footer class="abs footer"></footer>
<div class="abs center footer-logo">KR MEADOW CIRCLE</div>
<nav class="abs center footer-nav"><span>HOME</span><span>ABOUT US</span><span>SERVICES</span><span>BLOG</span><span>PRICING</span><span>CONTACT US</span></nav>
<div class="abs center contact-line">
  <span><svg width="12" height="12" viewBox="0 0 12 12"><path d="M2 1l2.5 0 1 3-1.5 1a7 7 0 003 3l1-1.5 3 1V10a1 1 0 01-1 1A10 10 0 011 2a1 1 0 011-1z" fill="#fff"/></svg>+65 9000 1234</span>
  <span><svg width="14" height="10" viewBox="0 0 14 10"><rect width="14" height="10" fill="#fff"/><path d="M0 0l7 5 7-5" stroke="#0d7a84" fill="none"/></svg>hello@meadowkrcircle.example</span>
  <span><svg width="12" height="12" viewBox="0 0 12 12"><path d="M11 1L1 5.5l4.2 1.3L6.5 11z" fill="#fff"/></svg>22 Larkspur Lane, Fairview, RI 02000</span>
</div>
<div class="abs center follow">Follow us <i></i><i></i><i class="red"></i><i></i></div>
<div class="abs copyright">© Copyright 2018 Kr Meadow Circle. All Rights Reserved &nbsp;&nbsp;|&nbsp;&nbsp; Privacy Policy.</div>

</body>
</html>
```